A3 Poster & DL Flyer Design Project

We need a poster and flyer designed to advertise a Wine, Food and Live music event.
Event title is "A Sip of Fine Moments" and is put on by Harlow's Creek Wines. Date for the event is Sunday 21 April 2013
The outdoor event covers wine, gourmet food and live music
Live music genera is Jazz, Blues, Swing
Updates

Project Deadline Extended
Reason: Most of the designs did not meet our requirements only 3 out of 21 have potential but would like to see more

Target Market(s)

25 - 55 wine drinkers with money.

Industry/Entity Type

Event

Requirements
Must have
• Title of the Event "A Sip of Fine Moments"
Date Sunday 21 April 2013 or be generic where we can write the date on each year.
Heron Logo
Entry is Free
No BYO Alcohol
Must reflect Wine, Food & Live Music

```html
<!DOCTYPE html>
<html lang="en">
<head>
<meta charset="utf-8">
<title>A Sip of Fine Moments – Poster</title>
<link rel="stylesheet" href="https://fonts.googleapis.com/css2?family=Arimo:wght@400;700&family=Libre+Baskerville&display=swap">
<style>
  :root {
    --page-bg: #efeeec;
    --band-blue: #6a9aad;
    --band-deep: #4f8298;
    --title-ink: #2b2b2b;
    --title-red: #e3202b;
    --byline-blue: #4c93b3;
    --seal-navy: #3e5a72;
    --ring-brown: #8a4535;
    --plank: #b48652;
    --plank-edge: #8a6237;
    --paper-top: #f6f6f6;
    --paper-bottom: #e4e5e6;
    --white: #ffffff;
  }
  html, body {
    margin: 0;
    width: 1200px;
    height: 882px;
    overflow: hidden;
    background: var(--page-bg);
  }
  .poster {
    position: absolute;
    left: 334px;
    top: 31px;
    width: 532px;
    height: 820px;
    box-shadow: 0 2px 8px rgba(0,0,0,.18);
  }
  .sans { font-family: "Arimo", Arial, sans-serif; }
  .serif { font-family: "Libre Baskerville", Georgia, serif; }
  .title { font-size: 37px; fill: var(--title-ink); }
  .title .accent { fill: var(--title-red); }
  .byline { font-size: 19px; fill: var(--byline-blue); }
  .brand { font-size: 9.5px; letter-spacing: 1px; fill: var(--title-ink); }
  .seal-text { font-size: 15px; fill: var(--white); letter-spacing: .5px; }
  .note { font-size: 11px; fill: var(--title-ink); }
  .menu-item { fill: var(--title-ink); }
  .plank-text { font-size: 15px; fill: var(--white); }
  .date { font-size: 23px; fill: var(--white); }
</style>
</head>
<body>
<svg class="poster" viewBox="0 0 415 640" xmlns="http://www.w3.org/2000/svg">
  <defs>
    <linearGradient id="paper" x1="0" y1="0" x2="0" y2="1">
      <stop offset="0" stop-color="var(--paper-top)"/>
      <stop offset="1" stop-color="var(--paper-bottom)"/>
    </linearGradient>
    <linearGradient id="bottles" x1="0" y1="0" x2="1" y2="0">
      <stop offset="0" stop-color="#2a1a1c"/>
      <stop offset=".55" stop-color="#4a3a34"/>
      <stop offset="1" stop-color="#e9e9ea" stop-opacity="0"/>
    </linearGradient>
  </defs>

  <!-- paper -->
  <rect class="paper" width="415" height="640" fill="url(#paper)"/>

  <!-- header band -->
  <g class="header-band">
    <path d="M0 0H415V60C320 62 200 78 0 92Z" fill="var(--band-blue)"/>
    <path d="M0 92C200 78 320 62 415 60V68C320 72 200 88 0 100Z" fill="var(--white)"/>
    <path d="M0 100C200 88 320 72 415 68V76C320 82 200 96 0 108Z" fill="var(--band-deep)"/>
    <g stroke="var(--white)" stroke-width="1.2" opacity=".8">
      <line x1="300" y1="0" x2="330" y2="55"/>
      <line x1="330" y1="0" x2="345" y2="50"/>
      <line x1="360" y1="0" x2="362" y2="48"/>
      <line x1="390" y1="0" x2="380" y2="45"/>
      <line x1="410" y1="8" x2="395" y2="48"/>
    </g>
  </g>

  <!-- brand -->
  <g class="brand-mark">
    <circle cx="24" cy="42" r="9" fill="var(--title-ink)"/>
    <text class="brand serif" x="40" y="46">HARLOW'S CREEK WINES</text>
  </g>

  <!-- entry seal -->
  <g class="entry-seal">
    <circle cx="346" cy="128" r="58" fill="var(--seal-navy)" stroke="var(--seal-navy)" stroke-width="6" stroke-dasharray="3 3"/>
    <circle cx="346" cy="128" r="50" fill="none" stroke="var(--white)" stroke-width="1" stroke-dasharray="2 2" opacity=".7"/>
    <text class="seal-text serif" x="346" y="113" text-anchor="middle">ENTRY</text>
    <text class="seal-text serif" x="346" y="134" text-anchor="middle">IS</text>
    <text class="seal-text serif" x="346" y="155" text-anchor="middle">FREE</text>
  </g>

  <!-- title -->
  <text class="title sans" x="19" y="150">A <tspan class="accent">Sip</tspan></text>
  <text class="title sans" x="19" y="190">of <tspan class="accent">Fine</tspan> Moments</text>
  <text class="byline sans" x="19" y="219">by Harlow's Creek Wines</text>

  <!-- bottles photo area -->
  <rect class="bottles-photo" x="0" y="245" width="200" height="330" fill="url(#bottles)" role="img" aria-label="Photo of two wine bottle necks, red and white wine"/>

  <!-- no BYO note -->
  <text class="note serif" x="396" y="224" text-anchor="middle">No</text>
  <text class="note serif" x="370" y="238" text-anchor="middle">BYO Alcohol</text>
  <path d="M341 287C360 287 372 268 376 250" fill="none" stroke="var(--title-ink)" stroke-width="1"/>
  <path d="M372 254L376 248L380 255" fill="none" stroke="var(--title-ink)" stroke-width="1"/>

  <!-- offering ring -->
  <g class="offering-ring">
    <circle cx="313" cy="330" r="77" fill="var(--white)" stroke="var(--ring-brown)" stroke-width="5" stroke-dasharray="6 2" stroke-linecap="round"/>
    <circle cx="313" cy="330" r="69" fill="none" stroke="var(--ring-brown)" stroke-width=".8" stroke-dasharray="1.5 2"/>
    <text class="menu-item sans" x="313" y="295" text-anchor="middle" font-size="19">Wine</text>
    <text class="menu-item sans" x="313" y="333" text-anchor="middle" font-size="16">Gourmet Food</text>
    <text class="menu-item sans" x="313" y="369" text-anchor="middle" font-size="16">Live Music</text>
  </g>
  <path d="M266 364C238 372 232 395 242 412" fill="none" stroke="var(--title-ink)" stroke-width="1"/>
  <path d="M237 406L243 414L247 405" fill="none" stroke="var(--title-ink)" stroke-width="1"/>

  <!-- genre planks -->
  <g class="genre-planks">
    <line x1="278" y1="390" x2="278" y2="530" stroke="var(--plank-edge)" stroke-width="1.2"/>
    <line x1="358" y1="390" x2="358" y2="530" stroke="var(--plank-edge)" stroke-width="1.2"/>
    <rect x="243" y="417" width="144" height="24" rx="2" fill="var(--plank)" stroke="var(--plank-edge)"/>
    <rect x="244" y="448" width="146" height="24" rx="2" fill="var(--plank)" stroke="var(--plank-edge)"/>
    <rect x="240" y="480" width="142" height="24" rx="2" fill="var(--plank)" stroke="var(--plank-edge)"/>
    <rect x="239" y="511" width="146" height="24" rx="2" fill="var(--plank)" stroke="var(--plank-edge)"/>
    <text class="plank-text sans" x="313" y="434" text-anchor="middle" font-weight="700">Genera</text>
    <text class="plank-text sans" x="315" y="465" text-anchor="middle">Jazz</text>
    <text class="plank-text sans" x="311" y="497" text-anchor="middle">Blues</text>
    <text class="plank-text sans" x="312" y="528" text-anchor="middle">Swing</text>
  </g>

  <!-- footer band -->
  <g class="footer-band">
    <path d="M0 545C120 530 260 540 415 552V640H0Z" fill="var(--band-blue)"/>
    <path d="M0 558C140 538 280 552 415 548V556C280 562 140 550 0 572Z" fill="var(--white)"/>
    <path d="M0 578C150 560 290 566 415 562" fill="none" stroke="var(--white)" stroke-width="1.5" opacity=".8"/>
  </g>
  <text class="date sans" x="207" y="620" text-anchor="middle">Sunday 21 April 2013</text>
</svg>
</body>
</html>
```